RKT Advisory Business Cards

Hi there,

I'd like to make a simple new business card design with the logo we already have created for our business.

I need a double sided business card with our logo on the front side and the company and person's details on the back side.

I'd like it to be on a white background and no background so I can potentially use it with either white paper or put it on different coloured paper in accordance with our business colours.

Please use the logo images I have attached and also the fonts.

So Front side:
- Logo in centre of business card (use medium logo so there is a pretty decent border around it, so don't want to fill the whole card but to make it prominent).

Back Side.
- We need 3 different business cards with the different people's name on each.

ie.

Dorian Valecki
Business Development Manager

m +61 455 207 318
e dorian@rktadvisory.example.com.au
w rktadvisory.example.com.au

- Also I'd like to put only the cog/power button logo in the top right hand corner of the card.
(You might need to chop the current logo in half as I don't have a seperate log just for this)
- Also I'd like some lines running on the top left hand corner diagonally, anything that will add to the design or some swirling lines that add some cool effect to the card.

Also I'd like to maybe put our ABN in the bottom right hand corner of the card in a smaller font.

I'd like to also talk to the designer if possible so I can get my idea across a bit better.

Thanks!

Regards,
Dorian

```html
<!DOCTYPE html>
<html lang="en">
<head>
<meta charset="utf-8">
<title>RKT Advisory – Business Card</title>
<link href="https://fonts.googleapis.com/css2?family=Exo+2:wght@700&family=Didact+Gothic&display=swap" rel="stylesheet">
<style>
  :root {
    --paper: #ffffff;
    --ink: #1c1c1c;
    --charcoal: #3b3b3b;
    --mark-grey: #4a4a4a;
    --orange: #f7941d;
    --stone: #cfcbbd;
  }
  html, body {
    margin: 0;
    padding: 0;
    width: 1200px;
    height: 741px;
    overflow: hidden;
    background: var(--paper);
  }
  .card {
    position: relative;
    width: 1200px;
    height: 741px;
    background: var(--paper);
    color: var(--ink);
    overflow: hidden;
  }
  .corner-accent {
    position: absolute;
    left: 0;
    top: 0;
  }
  .brand {
    position: absolute;
    top: 15px;
    right: 24px;
    display: flex;
    align-items: center;
    gap: 16px;
  }
  .brand-name {
    font-family: "Exo 2", sans-serif;
    font-weight: 700;
    font-size: 26px;
    color: var(--mark-grey);
    white-space: nowrap;
  }
  .brand-dot {
    width: 178px;
    height: 178px;
    border-radius: 50%;
    background: var(--mark-grey);
  }
  .holder-name {
    position: absolute;
    left: 276px;
    top: 222px;
    margin: 0;
    font-family: "Exo 2", sans-serif;
    font-weight: 700;
    font-size: 84px;
    line-height: 1;
    letter-spacing: 4px;
    white-space: nowrap;
    color: var(--ink);
  }
  .holder-role {
    position: absolute;
    left: 202px;
    top: 326px;
    margin: 0;
    font-family: "Didact Gothic", sans-serif;
    font-variant: small-caps;
    font-size: 42px;
    line-height: 1;
    letter-spacing: 12px;
    white-space: nowrap;
    color: var(--ink);
  }
  .contact {
    position: absolute;
    left: 71px;
    top: 562px;
    margin: 0;
    padding: 0;
    list-style: none;
    font-family: "Didact Gothic", sans-serif;
    font-variant: small-caps;
    font-size: 31px;
    letter-spacing: 6.4px;
    line-height: 44px;
    white-space: nowrap;
    color: var(--ink);
  }
  .contact .label {
    margin-right: 8px;
  }
  .contact .phone {
    letter-spacing: 11px;
  }
  .abn {
    position: absolute;
    left: 779px;
    top: 638px;
    margin: 0;
    font-family: "Didact Gothic", sans-serif;
    font-size: 26px;
    letter-spacing: 8px;
    white-space: nowrap;
    color: var(--ink);
  }
</style>
</head>
<body>
  <main class="card">
    <svg class="corner-accent" width="224" height="251" viewBox="0 0 224 251" role="img" aria-label="Diagonal striped corner decoration in charcoal and orange">
      <defs>
        <linearGradient id="corner-tone" x1="0" y1="0" x2="1" y2="1">
          <stop offset="0" stop-color="var(--orange)"/>
          <stop offset="0.55" stop-color="var(--charcoal)"/>
          <stop offset="1" stop-color="var(--charcoal)"/>
        </linearGradient>
      </defs>
      <polygon points="0,0 224,0 0,251" fill="url(#corner-tone)"/>
    </svg>

    <div class="brand">
      <span class="brand-name">RKT Advisory</span>
      <span class="brand-dot"></span>
    </div>

    <h1 class="holder-name">Dorian Valecki</h1>
    <p class="holder-role">Business Development Manager</p>

    <ul class="contact">
      <li class="phone"><span class="label">m</span>+61 455 207 318</li>
      <li><span class="label">e</span>dorian@rktadvisory.example.com.au</li>
      <li><span class="label">w</span>rktadvisory.example.com.au</li>
    </ul>

    <p class="abn">ABN: 5120 7734 869</p>
  </main>
</body>
</html>
```